Keystone Trench Co Business Card*

Looking for a professional, clean and crisp business card

I am in the underground utilities industry and am just looking for a really impressive business card. I would like our card to be white with our symbol crisp and clear with it protruding. I also have a business partner that will require his name and info on the card once the design is set. I would like to have our website info on the card which is;
http://keystonetrenchco.example/

Contact Information for Business Card

Website, contact name, number and email

```html
<!DOCTYPE html>
<html lang="en">
<head>
<meta charset="utf-8">
<title>Keystone Trench Co – Business Card</title>
<link href="https://fonts.googleapis.com/css2?family=Oswald:wght@500&family=Roboto+Condensed:wght@400;500&display=swap" rel="stylesheet">
<style>
  :root {
    --backdrop: #b8b8b8;
    --card-white: #ffffff;
    --card-dark: #231f20;
    --ink: #231f20;
    --accent-blue: #3358a8;
    --accent-red: #e0202a;
    --divider: #9a9a9a;
  }
  * { margin: 0; padding: 0; box-sizing: border-box; }
  html, body { width: 1200px; height: 801px; overflow: hidden; }
  body {
    position: relative;
    background: var(--backdrop);
    font-family: "Roboto Condensed", "Arial Narrow", sans-serif;
    color: var(--ink);
  }
  .card {
    position: absolute;
    top: 274px;
    width: 443px;
    height: 264px;
    overflow: hidden;
  }
  .card--front { left: 153px; background: var(--card-white); }
  .card--back  { left: 625px; background: var(--card-dark); }

  .band { position: absolute; background: var(--ink); }
  .band--thin-top    { top: 76px; height: 2px; }
  .band--thick       { top: 82px; height: 26px; }
  .band--thin-bottom { top: 110px; height: 2px; }
  .band--left  { left: 0; width: 147px; }
  .band--right { left: 296px; right: 0; }

  .brand-name {
    position: absolute;
    width: 150px;
    text-align: center;
    font-family: "Oswald", "Arial Narrow", sans-serif;
    font-weight: 500;
    font-size: 24px;
    line-height: 1.05;
    text-transform: uppercase;
  }
  .card--front .brand-name { left: 146px; top: 70px; color: var(--ink); }
  .card--back .brand-name  { left: 147px; top: 105px; color: var(--card-white); }

  .contact-person {
    position: absolute;
    right: 242px;
    top: 205px;
    text-align: right;
    white-space: nowrap;
  }
  .contact-person__name {
    font-weight: 500;
    font-size: 17px;
    line-height: 1;
    text-transform: uppercase;
  }
  .contact-person__title {
    margin-top: 3px;
    font-size: 14px;
    line-height: 1;
    color: var(--accent-blue);
  }
  .contact-divider {
    position: absolute;
    left: 215px;
    top: 197px;
    width: 1px;
    height: 44px;
    background: var(--divider);
  }
  .contact-list {
    position: absolute;
    left: 229px;
    top: 194px;
    list-style: none;
    font-size: 14px;
    line-height: 16.5px;
  }
  .contact-list li { display: flex; align-items: center; gap: 4px; white-space: nowrap; }
  .contact-list svg { width: 13px; height: 13px; flex: none; }
  .contact-list .highlight { color: var(--accent-blue); }
</style>
</head>
<body>

<section class="card card--front" aria-label="Business card front">
  <div class="band band--thin-top band--left"></div>
  <div class="band band--thick band--left"></div>
  <div class="band band--thin-bottom band--left"></div>
  <div class="band band--thin-top band--right"></div>
  <div class="band band--thick band--right"></div>
  <div class="band band--thin-bottom band--right"></div>

  <p class="brand-name">Keystone<br>Trench Co</p>

  <div class="contact-person">
    <p class="contact-person__name">Daniel Harper</p>
    <p class="contact-person__title">Managing Director</p>
  </div>

  <div class="contact-divider"></div>

  <ul class="contact-list">
    <li>
      <svg viewBox="0 0 16 16" aria-hidden="true"><path fill="var(--accent-red)" d="M3.5 1.5l2.6 2.8-1.5 1.9c.9 2 2.6 3.7 4.6 4.6l1.9-1.5 2.8 2.6-1.6 2.3C7 14 2 9 1.3 3.1z"/></svg>
      <span>044-555 010 274</span>
    </li>
    <li>
      <svg viewBox="0 0 16 16" aria-hidden="true"><rect x="1" y="3" width="14" height="10" fill="var(--accent-red)"/><path d="M1.5 3.5L8 9l6.5-5.5" fill="none" stroke="#fff" stroke-width="1.3"/></svg>
      <span>info@mailhost.example</span>
    </li>
    <li>
      <svg viewBox="0 0 16 16" aria-hidden="true" fill="none" stroke="var(--accent-red)" stroke-width="1.3"><circle cx="8" cy="8" r="6.5"/><ellipse cx="8" cy="8" rx="3" ry="6.5"/><path d="M1.5 8h13M2.5 4.8h11M2.5 11.2h11"/></svg>
      <span>www.<span class="highlight">keystonetrenchco</span>.example</span>
    </li>
  </ul>
</section>

<section class="card card--back" aria-label="Business card back">
  <p class="brand-name">Keystone<br>Trench Co</p>
</section>

</body>
</html>
```